Redesign of business card for Cedar Ridge Mechanical

We are looking for a new design for our business cards for Cedar Ridge Mechanical. We are a plumbing & HVAC construction company, operating on the West Coast of Canada and USA. Logo attached.
Industry/Entity Type
Construction - Plumbing & HVAC
Contact Information for Business Card
Name, address, phone numbers, email, website address
Look and feel
Each slider illustrates characteristics of the customer's brand and the style your logo design should communicate.

```html
<!DOCTYPE html>
<html lang="en">
<head>
<meta charset="utf-8">
<title>Cedar Ridge Mechanical – Business Card</title>
<link rel="stylesheet" href="https://fonts.googleapis.com/css2?family=Open+Sans:wght@400;700&display=swap">
<style>
  :root {
    --backdrop: #d4d4d4;
    --ink: #000000;
    --paper: #ffffff;
    --steel: #8a8a8a;
    --card-radius: 24px;
  }
  * { margin: 0; padding: 0; box-sizing: border-box; }
  html, body {
    width: 1200px; height: 896px; overflow: hidden;
    background: var(--backdrop);
    font-family: "Open Sans", sans-serif;
  }
  .canvas { position: relative; width: 1200px; height: 896px; }

  .card {
    position: absolute;
    left: 334px;
    width: 528px;
    height: 300px;
    border-radius: var(--card-radius);
    overflow: hidden;
  }
  .card--back {
    top: 126px;
    background: linear-gradient(110deg, #4a4a4a 0%, #2a2a2a 35%, #0a0a0a 60%, #000 100%);
  }
  .card--front {
    top: 474px;
    height: 302px;
    background: var(--paper);
  }

  .card__wave { position: absolute; inset: 0; width: 100%; height: 100%; }

  .brand {
    position: absolute; left: 20px; top: 22px;
    display: flex; align-items: flex-start; gap: 12px;
  }
  .brand__square { width: 34px; height: 34px; background: var(--ink); flex: none; margin-top: 4px; }
  .brand__name {
    width: 190px;
    font-weight: 700; font-size: 22px; line-height: 1.15;
    color: var(--ink); text-transform: uppercase; letter-spacing: 0.5px;
  }

  .contact {
    position: absolute; right: 20px; top: 118px;
    text-align: right; color: var(--paper);
  }
  .contact__name { font-weight: 700; font-size: 18px; line-height: 22px; letter-spacing: 0.3px; }
  .contact__role { font-size: 13.5px; line-height: 18px; margin-bottom: 15px; }
  .contact__address { font-size: 12.5px; line-height: 18px; margin-bottom: 15px; }
  .contact__line {
    display: flex; justify-content: flex-end; align-items: center; gap: 6px;
    font-size: 12.5px; line-height: 19px;
  }
  .contact__icon { width: 12px; height: 12px; flex: none; }
</style>
</head>
<body>
<main class="canvas">

  <section class="card card--back" role="img" aria-label="Card reverse: repeating brand monogram pattern in glossy black"></section>

  <section class="card card--front">
    <svg class="card__wave" viewBox="0 0 897 513" preserveAspectRatio="none" aria-hidden="true">
      <path d="M0,318 C40,370 110,392 210,396 C140,400 50,395 0,380 Z" fill="var(--ink)"/>
      <path d="M0,378 C60,402 150,412 250,410" fill="none" stroke="var(--steel)" stroke-width="7"/>
      <path d="M0,398 C150,440 300,420 420,330 C560,220 700,110 897,168" fill="none" stroke="var(--steel)" stroke-width="16"/>
      <path d="M0,418 C150,456 300,436 430,346 C570,240 710,140 897,188 L897,513 L0,513 Z" fill="var(--ink)"/>
    </svg>

    <div class="brand">
      <span class="brand__square"></span>
      <span class="brand__name">Cedar Ridge Mechanical</span>
    </div>

    <div class="contact">
      <p class="contact__name">DANIEL MOORE</p>
      <p class="contact__role">Managing Director</p>
      <p class="contact__address">Your address, City<br>State, Zip 1234</p>
      <p class="contact__line">604 555 0187
        <svg class="contact__icon" viewBox="0 0 24 24" aria-hidden="true"><path fill="#fff" d="M6.6 10.8a15 15 0 0 0 6.6 6.6l2.2-2.2a1 1 0 0 1 1-.25 11.4 11.4 0 0 0 3.6.57 1 1 0 0 1 1 1V20a1 1 0 0 1-1 1A17 17 0 0 1 3 4a1 1 0 0 1 1-1h3.5a1 1 0 0 1 1 1c0 1.25.2 2.45.57 3.57a1 1 0 0 1-.25 1z"/></svg>
      </p>
      <p class="contact__line">info@cedarridgemech.com
        <svg class="contact__icon" viewBox="0 0 24 24" aria-hidden="true"><rect x="2" y="5" width="20" height="14" rx="1.5" fill="#fff"/><path d="M3 6l9 7 9-7" fill="none" stroke="#000" stroke-width="1.8"/></svg>
      </p>
      <p class="contact__line">www.cedarridgemech.com
        <svg class="contact__icon" viewBox="0 0 24 24" aria-hidden="true"><circle cx="12" cy="12" r="10" fill="#fff"/><path d="M2 12h20M12 2c3 3 3 17 0 20M12 2c-3 3-3 17 0 20" fill="none" stroke="#000" stroke-width="1.5"/></svg>
      </p>
    </div>
  </section>

</main>
</body>
</html>
```